UI/ UX Design for ERP Software

We need a new UX/UI interface for a ERP software for property managers. Our CMMS / ERP solution is made based on responsive design technologies and is coded in PHP.
The overall UX to be similar to Tev Ulna - easy navigation, intuitive menus.

Industry/Entity Type

Property Management

Number of Pages Required

5+ page

Requirements
Must have
• Round dock buttons
Consistent icons across the application
Enough Spacing between buttons/icons/ menu
Consistent Font
Nice to have
• We would like the UX to allow the users to use the application without /minimum training.
Should not have
• we don't want anything that is classic with respect to UX

```html
<!DOCTYPE html>
<html lang="en">
<head>
<meta charset="utf-8">
<title>Crest Tower – General Info</title>
<link rel="stylesheet" href="https://fonts.googleapis.com/css2?family=Poppins:wght@400;500;600;700&display=swap">
<style>
  :root{
    --blue:#0b80f0;
    --blue-light:#1aa8f6;
    --ink:#3b4658;
    --ink-soft:#6c7483;
    --label:#3f4a5b;
    --page:#eef0f3;
    --card:#ffffff;
    --stripe:#f2f3f6;
    --nav-bg:#ffffff;
    --line:#e4e7ec;
  }
  *{box-sizing:border-box;margin:0;padding:0}
  html,body{width:1200px;height:800px;overflow:hidden}
  body{font-family:"Poppins",sans-serif;background:var(--page);color:var(--ink);position:relative}

  .topbar{height:65px;background:linear-gradient(90deg,var(--blue),var(--blue-light));display:flex;align-items:center;padding:0 36px;color:#fff;position:relative}
  .brand{display:flex;align-items:center;gap:9px;font-size:27px;font-weight:600;width:243px}
  .brand-mark{width:22px;height:22px;background:#fff;border-radius:5px}
  .search{display:flex;align-items:center;gap:12px;font-size:15px;color:rgba(255,255,255,.85)}
  .user{position:absolute;right:36px;top:0;height:65px;display:flex;align-items:center}
  .settings{width:38px;height:38px;border-radius:50%;background:rgba(255,255,255,.2);display:flex;align-items:center;justify-content:center;margin-right:10px}
  .avatar{width:37px;height:37px;border-radius:50%;background:linear-gradient(135deg,#3a3f4a,#c9a38a)}
  .user-meta{margin-left:9px;line-height:1.05}
  .user-name{font-size:15px;font-weight:600}
  .user-role{font-size:10px;font-weight:500}
  .user-caret{margin-left:14px}

  .mainnav{height:48px;background:var(--nav-bg);display:flex;align-items:center;justify-content:space-between;padding:0 38px 0 35px;box-shadow:0 1px 4px rgba(0,0,0,.04)}
  .mainnav a{font-size:13px;font-weight:500;color:var(--ink);text-decoration:none}
  .mainnav a.is-active{color:var(--blue);font-weight:600;font-size:14px}

  .page-head{display:flex;justify-content:space-between;align-items:center;padding:0 36px 0 34px;height:70px}
  .page-title{font-size:27px;font-weight:600;color:#4a5160}
  .crumbs{display:flex;align-items:center;gap:7px;font-size:13px;font-weight:500;color:#505a6a}

  .card{position:absolute;left:36px;top:186px;width:1128px;height:640px;background:var(--card);border-radius:7px}
  .section-title{position:absolute;font-size:18.5px;font-weight:600;color:#444c5a}
  .info-title{left:30px;top:32px}
  .gallery-title{left:803px;top:30px}
  .btn-edit{position:absolute;left:616px;top:25px;width:150px;height:37px;border-radius:19px;background:linear-gradient(90deg,#0b78ee,#14a2f5);color:#fff;font-size:12.5px;font-weight:600;display:flex;align-items:center;justify-content:center;gap:6px;letter-spacing:.3px}

  .info-table{position:absolute;left:30px;top:82px;width:737px;border-collapse:collapse;font-size:12.5px}
  .info-table td{height:35.5px;padding:0;vertical-align:middle}
  .info-table tr:nth-child(even) td{background:var(--stripe)}
  .info-table tr:nth-child(even) td:first-child{border-radius:4px 0 0 4px}
  .info-table tr:nth-child(even) td:last-child{border-radius:0 4px 4px 0}
  .info-table .lbl{color:var(--label);font-weight:500;padding-left:16px}
  .info-table .val{color:var(--ink-soft)}

  .gallery{position:absolute;left:805px;top:79px;width:287px;display:flex;flex-direction:column;gap:9px}
  .photo{height:213px;border-radius:5px}
  .photo-a{background:linear-gradient(180deg,#7fb4e6 0%,#d9dde2 45%,#5f5a58 75%,#3f6a34 100%)}
  .photo-b{background:linear-gradient(180deg,#3d89d6 0%,#c7c7c4 40%,#8b7d6c 70%,#5d7a45 100%)}
  .photo-c{background:linear-gradient(180deg,#2f6fc2 0%,#6aa0dc 50%,#e8e9ec 100%)}
</style>
</head>
<body>
  <header class="topbar">
    <div class="brand"><span class="brand-mark"></span>Lotbase</div>
    <div class="search">
      <svg width="18" height="18" viewBox="0 0 24 24" fill="none" stroke="#fff" stroke-width="2.5"><circle cx="10" cy="10" r="7"/><path d="M15.5 15.5L21 21" stroke-linecap="round"/></svg>
      Search...
    </div>
    <div class="user">
      <div class="settings">
        <svg width="20" height="20" viewBox="0 0 24 24" fill="#fff"><path d="M12 8.5a3.5 3.5 0 100 7 3.5 3.5 0 000-7zm9 5.2v-3.4l-2.5-.5a7 7 0 00-.7-1.7l1.4-2.1-2.4-2.4-2.1 1.4a7 7 0 00-1.7-.7L12.5 2h-3.4l-.5 2.5a7 7 0 00-1.7.7L4.8 3.8 2.4 6.2l1.4 2.1a7 7 0 00-.7 1.7L.6 10.3v3.4l2.5.5a7 7 0 00.7 1.7l-1.4 2.1 2.4 2.4 2.1-1.4a7 7 0 001.7.7l.5 2.5h3.4l.5-2.5a7 7 0 001.7-.7l2.1 1.4 2.4-2.4-1.4-2.1a7 7 0 00.7-1.7z" transform="translate(1 0) scale(.92)"/></svg>
      </div>
      <div class="avatar" role="img" aria-label="User profile photo"></div>
      <div class="user-meta">
        <div class="user-name">Dana Reyes</div>
        <div class="user-role">CEO founder</div>
      </div>
      <svg class="user-caret" width="12" height="8" viewBox="0 0 12 8" fill="none" stroke="#fff" stroke-width="2"><path d="M1 1.5l5 5 5-5"/></svg>
    </div>
  </header>

  <nav class="mainnav">
    <a class="is-active" href="#">General Info</a>
    <a href="#">Organization Chart</a>
    <a href="#">Tenant List</a>
    <a href="#">Property Assets</a>
    <a href="#">Contractors List</a>
    <a href="#">Compliance Manag...</a>
    <a href="#">Maint. Work Orders</a>
    <a href="#">Work Orders</a>
    <a href="#">Purchase Orders</a>
    <a href="#">Files</a>
  </nav>

  <div class="page-head">
    <h1 class="page-title">Crest Tower</h1>
    <div class="crumbs">
      <svg width="16" height="14" viewBox="0 0 16 14" fill="#505a6a"><path d="M8 0l8 7h-2.5v7h-4v-4.5h-3V14h-4V7H0z"/></svg>
      HOME <span>/</span> PROPERTIES
    </div>
  </div>

  <main class="card">
    <h2 class="section-title info-title">General Information</h2>
    <div class="btn-edit">
      <svg width="15" height="15" viewBox="0 0 16 16" fill="none" stroke="#fff" stroke-width="1.8"><path d="M7 2H2v12h12V9"/><path d="M12.5 1.5l2 2L8 10H6V8z" fill="#fff"/></svg>
      PROPERTY EDIT
    </div>

    <table class="info-table">
      <colgroup><col style="width:178px"><col style="width:245px"><col style="width:171px"><col></colgroup>
      <tr><td class="lbl">PROVINCE:</td><td class="val">British Columbia</td><td class="lbl">PROVINCE:</td><td class="val">British Columbia</td></tr>
      <tr><td class="lbl">CITY:</td><td class="val">Elm Ridge</td><td class="lbl">CITY:</td><td class="val">Elm Ridge</td></tr>
      <tr><td class="lbl">ADDRESS:</td><td class="val">42 Harbour Lane, Westmere, BC</td><td class="lbl">ADDRESS:</td><td class="val">42 Harbour</td></tr>
      <tr><td class="lbl">GPS ADDRESS:</td><td class="val">48.5120437 : -121-40271800000005</td><td class="lbl">GPS ADDRESS:</td><td class="val">48.5120437 : R4k 2P8</td></tr>
      <tr><td class="lbl">POSTAL CODE:</td><td class="val">R4k 2P8</td><td class="lbl">POSTAL CODE:</td><td class="val">07/01/1980</td></tr>
      <tr><td class="lbl">DATE BUILT:</td><td class="val">07/01/1980</td><td class="lbl">DATE BUILT:</td><td class="val">150000.00</td></tr>
      <tr><td class="lbl">AREA (SQ.FT):</td><td class="val">150000.00</td><td class="lbl">AREA (SQ.FT):</td><td class="val"></td></tr>
      <tr><td class="lbl">LOT SIZE:</td><td class="val"></td><td class="lbl">LOT SIZE:</td><td class="val">CDI</td></tr>
      <tr><td class="lbl">ZONING:</td><td class="val">CDI</td><td class="lbl">ZONING:</td><td class="val">Seel and concreate</td></tr>
      <tr><td class="lbl">STRUCTURE TYPE:</td><td class="val">Seel and concreate</td><td class="lbl">STRUCTURE TYPE:</td><td class="val">250</td></tr>
      <tr><td class="lbl">BUILDING HEIGHT:</td><td class="val">250</td><td class="lbl">BUILDING HEIGHT:</td><td class="val"></td></tr>
      <tr><td class="lbl">CLEAR HEIGHT:</td><td class="val"></td><td class="lbl">CLEAR HEIGHT:</td><td class="val">50</td></tr>
      <tr><td class="lbl">FLOOR LOADING CAPACITY:</td><td class="val">50</td><td class="lbl">FLOOR LOADING CAPACITY:</td><td class="val">30</td></tr>
      <tr><td class="lbl">NUMBER OF FLOORS:</td><td class="val">30</td><td class="lbl">NUMBER OF FLOORS:</td><td class="val">150</td></tr>
      <tr><td class="lbl">SUITES</td><td class="val">150</td><td class="lbl">SUITES</td><td class="val"></td></tr>
    </table>

    <h2 class="section-title gallery-title">General Information</h2>
    <div class="gallery">
      <div class="photo photo-a" role="img" aria-label="Photo of a modern two-storey house with garden and gate"></div>
      <div class="photo photo-b" role="img" aria-label="Photo of a modern house with stone cladding and balcony"></div>
      <div class="photo photo-c" role="img" aria-label="Photo of a white modern residence against blue sky"></div>
    </div>
  </main>
</body>
</html>
```